Coaching landingpage/salespage need a layout

Hi!
We are two people from Sweden looking for help to design our coaching landingpage/salespage.

What about:
We need a nice modern timeless appealing Photoshop layout (landingpage) for our coaching page where we coach people to “how to get a richer lifestyle”.

Style of page:
We want the site to reflect seriousness but still harmonic. We would like somewhat colorful and (but not too crazy). After all, we are coaching about investments and private economy.
Responsive layout – consider stacking order when scaling down window width. Fullpage-design where content areas are 960 grid/max-width.

----------------------------------------------------------------------------
Content on page:
*Headersection – Logo and header image with the two coaches together and space for later on adding a video.

*On the landingpage the customers can read up on what we mean by a richer lifestyle (use dummy text). We show our Vardagskompassen (= Lifestyle matrix) and a little description about that. If the customers want to know more, they can click "read more (or a symbolic icon that relates to read more)" to expand a hidden div (section) where they can read more about Vardagskompassen. They can also minimize the section.

*3-4 Unique selling points “Four reasons why choose coaching” with nice designed number-icons and some place for text.

*The customer should also be able to read something about what happens during a typical coaching session, some bullets that summarize it (use dummy text) and a couple of headlines, maybe 3 or 4 (about what they need to prepare for themselves .eg Skype, headset/microphone etc).

*Offer/product section: A section where the customer can see what services we provide, choose product and click order. When customer click order they will arrive to an order-page (this one you don’t have to design) .
Our products are as followed: Bronze (single coaching session), Silver (small-package), Gold (large-package). Use provided graphics for these products.

*Testimonials section. Currently we have 2 good testimonials, but only with text no portrait picture.

Testimonial1: “Uppiggande och inspirerande! Kommer med enkla vardagstips såväl som svårare tips. Ett roligt sätt att få en spark i baken, så att ekonomi-energin bibehålls! Tack för ett bra samtal!" - Helena Brattvik

Testimonial2: "Värdefullast för mig var kunskapen om alternativa investeringssställen som inte är börs eller eget ägande." - Annika Sjöstedt

*Section with portraits and info about the coaches (currently 2 coaches, but in future will be several, so a design-section that’s lets us add more coaches).

*Footer-section
------------------------------------------------------------------------

Colors:
Use Vardagskompassen (attached file) as colorinspiration. Doesn’t have to be exactly those colors, you can use similar colors if it is more pleasing to the eye and you can also use complementary colors.

Currently we have tried of our own but don't really nail it with any apealing design. This is what we have done so far but we want to replace it with your more professional design:

https://www.harborkite.se/full/Page/coaching13
-------------------------------------------------------------

SUMMARIZE of the above design-description:

* Our logo (attached psd-file with smart-object. You can try different colors with color-overlay)

*Apealing headerimage with portrait (attached file "big_portrait")

*Introduction text (use dummy text about 100 words)

*Text about Vardagskompassen (use dummy text about 200 words)

*Vardagskompassen (attached psd-file with smart-object)

*What we are covering during a coaching session (dummy text about 200 words and about 5 or 6 bullets)

*3-4 Unique Selling Points with stylish number icons (not 2 small) and some text.
*Our offers Bronze, Silver, Gold (attached pictures)
*Testimonials
*Picture & info about coaches (attached pictures, choose whichever suits you)
*Footer

Please comment if there are questions.

Target Market(s)

People who want to learn how to create a richer lifestyle which involves more freedom and a better well-being

Number of Pages Required

1 page

Font styles to use
Sans Serif
Other font styles liked:
• Roboto

Requirements
Should not have
• A cheezy unmodern landingpage with lots of texts and 10 sign-up buttons.
• This page is not a site about capturing emails and building lists by provide a "best-guide-for-something". It´s about getting people to book and pay for one or more coaching-sessions.

```html
<!DOCTYPE html>
<html lang="en">
<head>
<meta charset="utf-8">
<title>Harbor Kite – Lifestyle Coaching</title>
<link rel="stylesheet" href="https://fonts.googleapis.com/css2?family=Lato:wght@300;400;700;900&family=Montserrat:wght@400;600;700&display=swap">
<style>
:root{
  --blue:#29a6e0;
  --blue-dark:#1e8fc4;
  --team-blue:#2394c9;
  --green-1:#25a06a;
  --green-2:#2fc08e;
  --text:#333;
  --muted:#555;
  --heading:#444;
  --grey-btn:#777;
  --brown:#8d6b57;
  --rat:#1fa0dc;
  --orange:#f6a623;
  --freedom:#28a74b;
  --star:#f5a623;
  --footer:#050505;
  --card:#fff;
  --light:#eef2f5;
}
*{box-sizing:border-box;margin:0;padding:0}
html,body{width:1200px;height:3448px;overflow:hidden}
body{font-family:'Lato',sans-serif;color:var(--text);background:#fff;position:relative}
.wrap{width:860px;margin:0 auto;position:relative;height:100%}
section,header,footer{position:relative;width:1200px}

/* top bar */
.topbar{height:85px;background:var(--blue);color:#fff}
.brand{position:absolute;left:0;top:22px;display:flex;align-items:center;gap:14px;font-family:'Montserrat',sans-serif;font-weight:400;font-size:30px;letter-spacing:3px;color:#fff}
.brand-mark{width:38px;height:38px;background:#fff}
.contact-chip{position:absolute;top:18px;display:flex;gap:12px;align-items:center;font-family:'Montserrat',sans-serif}
.contact-chip .ico{width:46px;height:46px;border:2px solid #fff;border-radius:4px;display:flex;align-items:center;justify-content:center}
.contact-chip small{display:block;font-size:14px}
.contact-chip strong{display:block;font-size:19px;font-weight:600}
.chip-phone{left:430px}
.chip-mail{left:620px}

/* hero */
.hero{height:490px;background:linear-gradient(180deg,#4c7fb3 0%,#8fa7c4 25%,#e9b56a 45%,#f3a441 52%,#6b5a44 70%,#3c3a2c 100%)}
.hero-title{position:absolute;top:30px;width:100%;text-align:center;font-family:'Montserrat',sans-serif;font-weight:700;font-size:31px;color:#111;letter-spacing:.5px}

/* section heads */
.sec-title{text-align:center;font-weight:300;font-size:31px;color:var(--heading);letter-spacing:.5px}
.sec-title em{font-style:normal;color:var(--blue)}
.sec-title::after{content:"";display:block;width:56px;height:2px;background:var(--blue);margin:14px auto 0}
.sec-title.light{color:#fff}
.sec-title.light::after{background:#fff}

.btn{display:inline-block;background:var(--blue);color:#fff;font-family:'Montserrat',sans-serif;font-size:14px;font-weight:600;text-transform:uppercase;text-align:center;border-radius:2px}

/* about */
.about{height:310px;background:#fff;text-align:center}
.about .sec-title{padding-top:44px}
.about h3{margin-top:30px;font-size:15px;font-weight:900;color:#222}
.about p{margin:14px auto 0;width:840px;font-size:14.5px;line-height:29px;color:#333}
.about .btn{margin-top:18px;width:113px;height:37px;line-height:37px;font-size:13px}

/* matrix */
.matrix{height:559px;background:linear-gradient(135deg,#e4ebf0 0%,#f4f7f9 45%,#e7edf2 100%);text-align:center}
.matrix .sec-title{padding-top:44px}
.matrix .intro{margin:30px auto 0;width:840px;font-size:14.5px;line-height:29px;color:#333}
.pillars{position:absolute;top:226px;left:170px;width:860px;display:flex;justify-content:space-between}
.pillar{width:200px;text-align:center}
.pillar .circle{width:88px;height:88px;border-radius:50%;margin:0 auto;display:flex;align-items:center;justify-content:center}
.pillar h4{margin-top:26px;font-size:19px;font-weight:700;text-transform:uppercase}
.pillar p{margin-top:8px;font-size:14px;line-height:20px;color:#333}
.p-prosper .circle{background:var(--brown)} .p-prosper h4{color:var(--brown)}
.p-rat .circle{background:var(--rat)} .p-rat h4{color:var(--rat)}
.p-rich .circle{background:var(--orange)} .p-rich h4{color:var(--orange)}
.p-free .circle{background:var(--freedom)} .p-free h4{color:var(--freedom)}
.matrix .btn{position:absolute;left:520px;top:464px;width:161px;height:40px;line-height:40px;background:var(--grey-btn);font-size:13px}

/* products */
.products{height:637px;background:linear-gradient(150deg,var(--green-1) 0%,#239864 40%,var(--green-2) 100%);color:#fff;text-align:center}
.products .sec-title{padding-top:38px}
.products .lead{margin-top:30px;font-size:15px;line-height:24px}
.plans{position:absolute;top:220px;left:175px;width:850px;display:flex;justify-content:space-between}
.plan{width:262px;height:313px;background:var(--card);color:#111;text-align:center;position:relative}
.medal{width:100px;height:100px;border-radius:50%;margin:40px auto 0}
.medal.bronze{background:radial-gradient(circle at 40% 35%,#f0a35c,#c26a27 60%,#8e4a18)}
.medal.gold{background:radial-gradient(circle at 40% 35%,#ffe27a,#e6b420 60%,#b38410)}
.medal.silver{background:radial-gradient(circle at 40% 35%,#f2f2f2,#c5c5c5 60%,#959595)}
.plan h3{margin-top:22px;font-family:'Montserrat',sans-serif;font-size:19px;font-weight:600;text-transform:uppercase}
.plan p{font-size:17px;line-height:33px;margin-top:6px}
.plan p + p{margin-top:0}
.plan .btn{position:absolute;left:68px;bottom:-20px;width:126px;height:44px;line-height:44px;text-transform:none;font-size:15px;border:2px solid #fff}

/* testimonials */
.testimonials{height:397px;background:#fff}
.testimonials .sec-title{padding-top:36px}
.quotes{position:absolute;top:133px;left:172px;width:856px;display:flex;justify-content:space-between}
.quote{width:402px;height:165px;border:1px solid #ddd;padding:20px 24px;font-size:13.5px;line-height:19px;color:#555}
.quote .qm{color:#bbb;font-family:Georgia,serif;font-size:24px;line-height:10px;vertical-align:-6px;margin-right:4px}
.stars{margin-top:8px;color:var(--star);font-size:12px;letter-spacing:1px}
.quote cite{display:block;margin-top:6px;font-style:normal;color:var(--blue);font-size:13.5px}
.slider-line{position:absolute;top:341px;left:172px;width:856px;height:1px;background:#bbb}
.slider-line .right{position:absolute;left:444px;right:0;height:1px;background:var(--blue)}
.dot{position:absolute;top:-12px;width:24px;height:24px;border-radius:50%;display:flex;align-items:center;justify-content:center}
.dot.prev{left:418px;background:#777}
.dot.next{left:446px;background:var(--blue)}

/* team */
.team{height:626px;background:linear-gradient(160deg,#2a9fd3 0%,var(--team-blue) 50%,#1f86ba 100%)}
.team .sec-title{padding-top:40px}
.coaches{position:absolute;top:147px;left:175px;width:850px;display:flex;justify-content:space-between}
.coach{width:418px;height:423px;background:#f2f2f2;border-radius:6px;text-align:center;padding-top:30px}
.portrait{width:161px;height:161px;margin:0 auto;border:1px solid #999}
.portrait.one{background:linear-gradient(180deg,#b9a88e,#8f7b63)}
.portrait.two{background:linear-gradient(180deg,#5d5248,#2f2a26)}
.coach h3{margin-top:28px;font-weight:400;font-size:24px;color:#555}
.coach .mail{margin-top:10px;font-size:15px;color:#333;display:flex;align-items:center;justify-content:center;gap:8px}
.coach p{margin:16px auto 0;width:350px;font-size:13.5px;line-height:20px;color:#444}

/* footer */
.site-footer{height:322px;background:var(--footer);color:#fff}
.f-col{position:absolute;top:40px}
.f-col h4{font-family:'Montserrat',sans-serif;font-size:16px;font-weight:600;text-transform:uppercase;letter-spacing:.5px;padding-bottom:12px;border-bottom:1px solid #444}
.col-map{left:177px;width:290px}
.col-contact{left:552px;width:210px}
.col-form{left:802px;width:223px}
.map{margin-top:20px;width:290px;height:115px;background:linear-gradient(135deg,#e4e2dc,#d2d6d0)}
.col-contact .name{margin-top:20px;font-family:'Montserrat',sans-serif;font-size:13px;font-weight:600}
.col-contact .addr{margin-top:20px;font-size:13.5px;line-height:20px}
.col-contact .line{margin-top:20px;font-size:13.5px;display:flex;align-items:center;gap:8px}
.field{display:block;margin-top:10px;width:223px;height:34px;background:#fff;border:0;color:#555;font-size:12px;padding:0 10px;line-height:34px}
.field:first-of-type{margin-top:20px}
.submit{margin-top:14px;width:115px;height:30px;line-height:30px;font-size:12px}
.copyright{height:22px;background:var(--blue);color:#fff;font-size:11px;text-align:center;line-height:22px}
</style>
</head>
<body>

<header class="topbar">
  <div class="wrap">
    <div class="brand"><span class="brand-mark"></span>HARBOR KITE</div>
    <div class="contact-chip chip-phone">
      <span class="ico"><svg width="24" height="24" viewBox="0 0 24 24"><path d="M6.6 10.8c1.4 2.8 3.8 5.1 6.6 6.6l2.2-2.2c.3-.3.7-.4 1-.2 1.1.4 2.3.6 3.6.6.6 0 1 .4 1 1V20c0 .6-.4 1-1 1C10.6 21 3 13.4 3 4c0-.6.4-1 1-1h3.5c.6 0 1 .4 1 1 0 1.3.2 2.5.6 3.6.1.3 0 .7-.2 1z" fill="#fff"/></svg></span>
      <div><small>Call Us:</small><strong>555-010-2040</strong></div>
    </div>
    <div class="contact-chip chip-mail">
      <span class="ico"><svg width="24" height="20" viewBox="0 0 24 20"><rect x="1" y="2" width="22" height="16" fill="none" stroke="#fff" stroke-width="2"/><path d="M1 3l11 8 11-8" fill="none" stroke="#fff" stroke-width="2"/></svg></span>
      <div><small>Mail Us:</small><strong>team@harborkite.se</strong></div>
    </div>
  </div>
</header>

<section class="hero" role="img" aria-label="Header image: the two coaches shown in a video frame held in front of a sunset over a lake">
  <h1 class="hero-title">STEP BY STEP TO ONE RICHER LIFESTYLE</h1>
</section>

<section class="about">
  <h2 class="sec-title">ABOUT <em>LIFESTYLE COACHING</em></h2>
  <h3>STEP BY STEP TO ONE RICHER LIFESTYLE</h3>
  <p>Lifestyle Coaching is about finding out what creates a highly prosperous and high freedom in your life. It's about finding out what you really want with your life and then step by step to design a lifestyle around all this. A lifestyle that will last a lifetime and not just a short time and then fall back to your old way of life that does not give you the results you want .</p>
  <span class="btn">Read More</span>
</section>

<section class="matrix">
  <h2 class="sec-title">OUR <em>LIFESTYLE MATRIX</em></h2>
  <p class="intro">What is a richer lifestyle may differ between different people. It can also be quite difficult on their own to get a good picture of what you really mean by this . We have therefore developed a simple model to facilitate the understanding and the creation of a richer lifestyle. This is a model we call lifestyle matrix and consists of the following four parts representing respective lifestyle.</p>
  <div class="pillars">
    <div class="pillar p-prosper">
      <div class="circle"><svg width="44" height="40" viewBox="0 0 44 40"><path d="M22 36S4 24 4 13a9 9 0 0 1 18-3 9 9 0 0 1 18 3c0 11-18 23-18 23z" fill="#fff"/></svg></div>
      <h4>Prosperous</h4>
      <p>Lorem ipsum dolor sit am et, consectetuer sit ame Lorem ipsum dolor sit am</p>
    </div>
    <div class="pillar p-rat">
      <div class="circle"><svg width="44" height="44" viewBox="0 0 44 44"><circle cx="22" cy="22" r="14" fill="none" stroke="#fff" stroke-width="4"/><path d="M22 4l6 4-6 4z" fill="#fff"/></svg></div>
      <h4>Rat Race</h4>
      <p>Lorem ipsum dolor sit am et, consectetuer sit ame Lorem ipsum dolor sit am</p>
    </div>
    <div class="pillar p-rich">
      <div class="circle"><svg width="44" height="44" viewBox="0 0 44 44"><circle cx="22" cy="18" r="11" fill="none" stroke="#fff" stroke-width="3"/><path d="M8 34h28v4H8z" fill="#fff"/><text x="22" y="23" font-family="Lato,sans-serif" font-size="14" font-weight="700" fill="#fff" text-anchor="middle">$</text></svg></div>
      <h4>A Richer</h4>
      <p>Lorem ipsum dolor sit am et, consectetuer sit ame Lorem ipsum dolor sit am</p>
    </div>
    <div class="pillar p-free">
      <div class="circle"><svg width="44" height="40" viewBox="0 0 44 40"><path d="M4 16l14 6L40 6 24 34l-4-10z" fill="#fff"/></svg></div>
      <h4>Freedom</h4>
      <p>Lorem ipsum dolor sit am et, consectetuer sit ame Lorem ipsum dolor sit am</p>
    </div>
  </div>
  <span class="btn">Get Started</span>
</section>

<section class="products">
  <h2 class="sec-title light">OUR PRODUCTS</h2>
  <p class="lead">You want something you do not already have ?<br>Start when designing a lifestyle you have not previously lived . We, at Harbor Kite will help you with this by lifestyle<br>coaching. Below , you can choose one of our coaching packages .</p>
  <div class="plans">
    <div class="plan">
      <div class="medal bronze" role="img" aria-label="Bronze medal"></div>
      <h3>Disposable Session</h3>
      <p>Includes 1 Session</p>
      <p>Price 650 Sek</p>
      <span class="btn">Reserve</span>
    </div>
    <div class="plan">
      <div class="medal gold" role="img" aria-label="Gold medal"></div>
      <h3>Silverpaketet</h3>
      <p>Includes 5 Sessions</p>
      <p>Price 3050 Sek</p>
      <span class="btn">Reserve</span>
    </div>
    <div class="plan">
      <div class="medal silver" role="img" aria-label="Silver medal"></div>
      <h3>Guldpaketet</h3>
      <p>Includes 10 Sessions</p>
      <p>Price 5800 Sek</p>
      <span class="btn">Reserve</span>
    </div>
  </div>
</section>

<section class="testimonials">
  <h2 class="sec-title">CLIENTS <em>TESTIMONIALS</em></h2>
  <div class="quotes">
    <blockquote class="quote">
      <span class="qm">&ldquo;</span>Duis autem vel eum iriure dolor in hendrerit in vulputate velitj esse molestie consequat, vel illum dolore eu feugiat nulla facilin sis at vero eros Duis autem vel eum iriure dolor in
      <div class="stars">★★★★★</div>
      <cite>Helena Brattvik</cite>
    </blockquote>
    <blockquote class="quote">
      <span class="qm">&ldquo;</span>Duis autem vel eum iriure dolor in hendrerit in vulputate velitj esse molestie consequat, vel illum dolore eu feugiat nulla facilin sis at vero eros Duis autem vel eum iriure dolor in
      <div class="stars">★★★★★</div>
      <cite>Annika Sjöstedt</cite>
    </blockquote>
  </div>
  <div class="slider-line">
    <div class="right"></div>
    <span class="dot prev"><svg width="10" height="10" viewBox="0 0 10 10"><path d="M7 1L3 5l4 4" stroke="#fff" stroke-width="2" fill="none"/></svg></span>
    <span class="dot next"><svg width="10" height="10" viewBox="0 0 10 10"><path d="M3 1l4 4-4 4" stroke="#fff" stroke-width="2" fill="none"/></svg></span>
  </div>
</section>

<section class="team">
  <h2 class="sec-title light">OUR TEAM</h2>
  <div class="coaches">
    <div class="coach">
      <div class="portrait one" role="img" aria-label="Portrait of coach Mattias Lindqvar"></div>
      <h3>Mattias Lindqvar</h3>
      <div class="mail"><svg width="14" height="11" viewBox="0 0 14 11"><rect width="14" height="11" fill="#777"/><path d="M0 1l7 5 7-5" stroke="#f2f2f2" fill="none"/></svg>mattias@harborkite.se</div>
      <p>Mattias has a broad background in finance and IT . As an investor is his focus on dividend stocks, real estate and internet -based entrepreneurship . He also has a long experience and a passion to help people and businesses to evolve in different ways. Basically , this has always been about creating more good days in life.</p>
    </div>
    <div class="coach">
      <div class="portrait two" role="img" aria-label="Portrait of coach Joakim Westerholm"></div>
      <h3>Joakim Westerholm</h3>
      <div class="mail"><svg width="14" height="11" viewBox="0 0 14 11"><rect width="14" height="11" fill="#777"/><path d="M0 1l7 5 7-5" stroke="#f2f2f2" fill="none"/></svg>joakim@harborkite.se</div>
      <p>Versatile investors with a focus on alternative and high-risk investments Besides the stock market , investing in unlisted Joakim startup companies and various Internet-based investments such as P2P lending , online games and apps .</p>
    </div>
  </div>
</section>

<footer class="site-footer">
  <div class="f-col col-map">
    <h4>Location Map</h4>
    <div class="map" role="img" aria-label="Street map showing the office location"></div>
  </div>
  <div class="f-col col-contact">
    <h4>Contact Details</h4>
    <div class="name">HARBOR KITE</div>
    <div class="addr">Ekbackevägen 12<br>411 05 Göteborg</div>
    <div class="line"><svg width="12" height="12" viewBox="0 0 24 24"><path d="M6.6 10.8c1.4 2.8 3.8 5.1 6.6 6.6l2.2-2.2c.3-.3.7-.4 1-.2 1.1.4 2.3.6 3.6.6.6 0 1 .4 1 1V20c0 .6-.4 1-1 1C10.6 21 3 13.4 3 4c0-.6.4-1 1-1h3.5c.6 0 1 .4 1 1 0 1.3.2 2.5.6 3.6.1.3 0 .7-.2 1z" fill="#fff"/></svg>0555-010-204</div>
    <div class="line"><svg width="12" height="10" viewBox="0 0 14 11"><rect width="14" height="11" fill="#fff"/><path d="M0 1l7 5 7-5" stroke="#000" fill="none"/></svg>team@harborkite.se</div>
  </div>
  <div class="f-col col-form">
    <h4>Quick Inquiry</h4>
    <span class="field">Name</span>
    <span class="field">Message</span>
    <span class="field">Email</span>
    <span class="btn submit">Submit</span>
  </div>
</footer>
<div class="copyright">Copyright © 2016 HARBOR KITE . All Rights Reserved</div>

</body>
</html>
```